Talon Microsystems PowerPoint Master Slide Deck Design

This is a 2-phase project to design a slide deck for a semiconductor company in the Silicon Valley. The design budget will be increased with each phase.
The slide deck will need to have one version with a dark background for presentations and a second version with a white background. Otherwise, the slides will be the same. I anticipate we will need a total of 10 slides, but that number may change.
The first phase will be to design a Title and a Title and Content slide.
- The Title Slide is the first slide of the deck. It should include the presentation title, the presenter's name and date of presentation
- The Title and Content slide should include a title and content with bullet points and up to 2 additional sub-bullets
- The Title and Content slide should have a footer that includes the slide #, Talon Microsystems Confidential, and the logo. This footer will be on every slide except the Title Slide
The first two slides will serve as the format for the remaining ~8 slides:
-Header and Content Text (1, 2, 4 column)
-Header and Content Image (bar chart, pie chart, tables)
-Break
-Title only
-Closing (Talon logo only)
Our slides contain a lot of content so a clean and simple design is best.
Both phases will need to include pre-set color options for
-Text and Lines
-Shadows
-Bullets and sub-bullets (including shapes, ex. circle, slash, square, etc.)
-Bar charts, pie charts, tables
Samples of our collateral are attached. Logo files are also attached
Look and feel
Each slider illustrates characteristics of the customer's brand and the style your logo design should communicate.

```html
<!DOCTYPE html>
<html lang="en">
<head>
<meta charset="utf-8">
<title>Talon Microsystems Slide Deck</title>
<link rel="stylesheet" href="https://fonts.googleapis.com/css2?family=Poppins:wght@400;500;600;700;800&display=swap">
<style>
:root{
  --page:#f2f2f2;
  --white:#ffffff;
  --sky:#3cbff6;
  --sky-dark:#1f9fe0;
  --royal:#1e4fe8;
  --ink:#3a3a3a;
  --body:#6d6d6d;
  --shadow:0 4px 14px rgba(0,0,0,.12);
}
*{box-sizing:border-box;margin:0;padding:0}
html,body{width:1200px;height:4090px;overflow:hidden}
body{background:var(--page);font-family:'Poppins',sans-serif;position:relative}
.slide{position:absolute;width:1048px;height:590px;background:var(--white);box-shadow:0 2px 8px rgba(0,0,0,.08);overflow:hidden}
.card{position:absolute;left:71px;top:60px;width:902px;height:434px;background:var(--white);box-shadow:var(--shadow)}
.footer{position:absolute;left:0;bottom:0;width:100%;height:48px;background:var(--sky);color:var(--white);font-size:11px;display:flex;align-items:center;padding:0 71px}
.footer .conf{flex:1;text-transform:uppercase;letter-spacing:.2px}
.footer .meta{display:flex;align-items:center;gap:22px}
.brand-mini{display:flex;align-items:center;gap:5px;font-weight:600;font-size:13px}
.brand-mini i{width:8px;height:8px;border-radius:50%;background:var(--white);display:block}
.heading{position:absolute;color:var(--sky);font-weight:700;font-size:35px;line-height:1}
.copy{position:absolute;color:var(--body);font-size:12.6px;line-height:27px;text-align:justify}
.photo{position:absolute}
/* title slide */
.title-photo{left:0;top:0;width:608px;height:590px;background:linear-gradient(135deg,#0a3a4a 0%,#0f6f8f 40%,#0b2a44 75%,#061826 100%)}
.title-brand{position:absolute;left:654px;top:110px;display:flex;align-items:center;gap:12px;color:var(--ink);font-weight:600;font-size:46px;letter-spacing:1px}
.title-brand i{width:22px;height:22px;border-radius:50%;background:var(--royal);display:block}
.title-band{position:absolute;left:608px;top:263px;width:440px;height:173px;background:var(--sky);text-align:center;color:var(--white)}
.title-band h1{margin-top:38px;font-size:27px;font-weight:800;color:#4a4a4a}
.title-band .presenter{margin-top:12px;font-size:20px;font-weight:500}
.title-band .date{margin-top:8px;font-size:16px}
/* chart */
.bar{position:absolute;width:41px;background:linear-gradient(90deg,var(--sky) 70%,var(--sky-dark));box-shadow:2px 3px 6px rgba(0,0,0,.15)}
.bar span{position:absolute;bottom:14px;left:50%;transform:translateX(-50%) rotate(-90deg);transform-origin:center;color:var(--white);font-size:13px;font-weight:600;white-space:nowrap}
.bar-label{position:absolute;width:44px;height:44px;border-radius:50%;background:var(--white);box-shadow:var(--shadow);font-size:15px;font-weight:700;color:#222;display:flex;align-items:center;justify-content:center}
/* bullets */
.bullets{position:absolute;left:60px;top:112px;list-style:none;color:#333;font-size:16px}
.bullets li{position:relative;padding-left:26px;margin-bottom:24px}
.bullets li::before{content:"";position:absolute;left:0;top:5px;width:14px;height:14px;border-radius:50%;background:var(--sky)}
.bullets li.sub{margin-left:30px;padding-left:40px;line-height:24px;width:520px;margin-bottom:22px}
.bullets li.sub::before{background:none;border:1.5px solid var(--sky);top:6px}
.closing-brand{position:absolute;left:50%;top:50%;transform:translate(-50%,-50%);display:flex;align-items:center;gap:14px;color:var(--ink);font-weight:600;font-size:56px;letter-spacing:1px}
.closing-brand i{width:26px;height:26px;border-radius:50%;background:var(--royal);display:block}
</style>
</head>
<body>

<!-- Title -->
<section class="slide" style="left:76px;top:92px">
  <div class="photo title-photo" role="img" aria-label="Close-up of a glowing teal circuit board with a microchip"></div>
  <div class="title-brand"><i></i>TALON</div>
  <div class="title-band">
    <h1>LOREM IPSUM DOLOR SIT</h1>
    <div class="presenter">LOREM IPSUM</div>
    <div class="date">13/12/2023</div>
  </div>
</section>

<!-- Who we are -->
<section class="slide" style="left:76px;top:768px">
  <div class="card">
    <h2 class="heading" style="left:54px;top:64px">Who we are</h2>
    <p class="copy" style="left:54px;top:118px;width:376px">Sed ut perspiciatis unde omnis iste natus error sit voluptatem accusantium doloremque laudantium, totam rem aperiam, eaque ipsa quae ab illo inventore veritatis et quasi architecto beatae vitae dicta sunt explicabo. Nemo enim ipsam voluptatem quia voluptas sit aspernatur aut odit aut fugit, sed quia consequuntur magni dolores eos qui ratione voluptatem sequi nesciunt. Neque porro quisquam est, qui dolorem ipsum quia dolor sit amet, consectetur,</p>
    <p class="copy" style="left:468px;top:118px;width:376px">Sed ut perspiciatis unde omnis iste natus error sit voluptatem accusantium doloremque laudantium, totam rem aperiam, eaque ipsa quae ab illo inventore veritatis et quasi architecto beatae vitae dicta sunt explicabo. Nemo enim ipsam voluptatem quia voluptas sit aspernatur aut odit aut fugit, sed quia consequuntur magni dolores eos qui ratione voluptatem sequi nesciunt. Neque porro quisquam est, qui dolorem ipsum quia dolor sit amet, consectetur,</p>
  </div>
  <footer class="footer"><span class="conf">Talon Microsystems Confidential</span><span class="meta"><span class="brand-mini"><i></i>TALON</span><span>13.12.2023</span><span>I</span><span>02</span></span></footer>
</section>

<!-- What we do -->
<section class="slide" style="left:76px;top:1429px">
  <div class="card">
    <h2 class="heading" style="left:54px;top:64px">What we do</h2>
    <p class="copy" style="left:54px;top:118px;width:376px">Sed ut perspiciatis unde omnis iste natus error sit voluptatem accusantium doloremque laudantium, totam rem aperiam, eaque ipsa quae ab illo inventore veritatis et quasi architecto beatae vitae dicta sunt explicabo. Nemo enim ipsam voluptatem quia voluptas sit aspernatur aut odit aut fugit, sed quia consequuntur magni dolores eos qui ratione voluptatem sequi nesciunt. Neque porro quisquam est, qui dolorem ipsum quia dolor sit amet, consectetur,</p>
    <div style="position:absolute;left:492px;top:108px;width:330px;height:246px;background:var(--sky)"></div>
    <div class="photo" role="img" aria-label="Technician in a cleanroom suit inspecting a circuit board" style="left:505px;top:114px;width:335px;height:240px;background:linear-gradient(135deg,#1b4f86,#2f7fc4 45%,#0e2d55 80%,#b8892a)"></div>
  </div>
  <footer class="footer"><span class="conf">Talon Microsystems Confidential</span><span class="meta"><span class="brand-mini"><i></i>TALON</span><span>13.12.2023</span><span>I</span><span>03</span></span></footer>
</section>

<!-- Graphs -->
<section class="slide" style="left:76px;top:2086px">
  <div class="card">
    <div class="bar" style="left:68px;top:230px;height:124px"><span>2019</span></div>
    <div class="bar" style="left:136px;top:143px;height:211px"><span>2020</span></div>
    <div class="bar" style="left:204px;top:92px;height:262px"><span>2021</span></div>
    <div class="bar" style="left:273px;top:230px;height:124px"><span>2022</span></div>
    <div class="bar" style="left:341px;top:275px;height:79px"><span>2023</span></div>
    <div class="bar-label" style="left:67px;top:208px">50%</div>
    <div class="bar-label" style="left:135px;top:121px">80%</div>
    <div class="bar-label" style="left:203px;top:70px">90%</div>
    <div class="bar-label" style="left:272px;top:208px">50%</div>
    <div class="bar-label" style="left:340px;top:253px">40%</div>
    <h2 class="heading" style="left:476px;top:120px">Graphs</h2>
    <p class="copy" style="left:476px;top:192px;width:376px">Sed ut perspiciatis unde omnis iste natus error sit voluptatem accusantium doloremque laudantium, totam rem aperiam, eaque ipsa quae ab illo inventore veritatis et quasi architecto beatae vitae dicta sunt explicabo. Nemo enim ipsam voluptatem quia voluptas sit aspernatur aut odit aut fugit,</p>
  </div>
  <footer class="footer"><span class="conf">Talon Microsystems Confidential</span><span class="meta"><span class="brand-mini"><i></i>TALON</span><span>13.12.2023</span><span>I</span><span>04</span></span></footer>
</section>

<!-- Case studies -->
<section class="slide" style="left:81px;top:2751px">
  <div class="card">
    <div class="photo" role="img" aria-label="Blue circuit board traces fading into white" style="left:300px;top:0;width:602px;height:434px;background:linear-gradient(90deg,rgba(255,255,255,1) 0%,rgba(220,232,242,.9) 30%,#7fa9cc 60%,#2f6fa6 85%,#1d5590 100%)"></div>
    <h2 class="heading" style="left:60px;top:58px">Case Studies</h2>
    <ul class="bullets">
      <li>Lorem ipsum dolor sit amet, consectetur</li>
      <li>Lorem ipsum dolor sit amet, consectetur</li>
      <li style="margin-bottom:30px">Lorem ipsum dolor sit amet, consectetur</li>
      <li class="sub">Lorem ipsum dolor sit amet, consectetur adipiscing elit, sed do eiusmod tempor</li>
      <li class="sub">Lorem ipsum dolor sit amet, consectetur adipiscing elit, sed do eiusmod tempor</li>
    </ul>
  </div>
  <footer class="footer"><span class="conf">Talon Microsystems Confidential</span><span class="meta"><span class="brand-mini"><i></i>TALON</span><span>13.12.2023</span><span>I</span><span>05</span></span></footer>
</section>

<!-- Closing -->
<section class="slide" style="left:81px;top:3406px">
  <div class="photo" role="img" aria-label="Pale blue circuit board background" style="left:68px;top:76px;width:900px;height:430px;background:linear-gradient(160deg,#dfeef8 0%,#c7dced 45%,#e3e8ee 100%)">
    <div class="closing-brand"><i></i>TALON</div>
  </div>
</section>

</body>
</html>
```